Process Serving Company needs a letterhead design

Looking to have a letterhead designed for letters to attorneys advertising our business. We would like something eye catching but professional. Colors and logos are attached. Please add "Process Service and Attorney Support" near the logo or header

Target Market(s)

Attorneys

Font styles to use
Serif
Sans Serif

Colors
33a6d7
0255a3
85cae6
cee9f5
ecf7fb

```html
<!DOCTYPE html>
<html lang="en">
<head>
<meta charset="utf-8">
<title>Mesa Swift Serve Letterhead</title>
<link href="https://fonts.googleapis.com/css2?family=Open+Sans:wght@400;600&family=Montserrat:wght@600&display=swap" rel="stylesheet">
<style>
  :root {
    --brand-blue: #33a6d7;
    --brand-deep: #0e87c8;
    --ink: #3a3a3a;
    --rule: #5a5a5a;
    --paper-top: #ffffff;
    --paper-bottom: #f1f2f3;
    --tint: #ecf7fb;
  }
  * { box-sizing: border-box; margin: 0; padding: 0; }
  html, body { width: 1063px; height: 1200px; overflow: hidden; }
  body {
    font-family: "Open Sans", Arial, sans-serif;
    color: var(--ink);
  }
  .letterhead {
    position: relative;
    width: 1063px;
    height: 1200px;
    background: linear-gradient(180deg, var(--paper-top) 45%, var(--paper-bottom) 100%);
  }
  .brand {
    position: absolute;
    left: 78px;
    top: 150px;
    display: flex;
    align-items: center;
    gap: 14px;
  }
  .brand-square {
    width: 46px;
    height: 46px;
    background: var(--brand-blue);
  }
  .brand-name {
    font-family: "Open Sans", Arial, sans-serif;
    font-weight: 400;
    font-size: 30px;
    letter-spacing: 1px;
    color: var(--brand-blue);
    text-transform: uppercase;
    line-height: 1.05;
  }
  .contact {
    position: absolute;
    left: 735px;
    top: 62px;
    font-size: 14px;
    line-height: 19px;
    color: var(--ink);
  }
  .contact-line { display: flex; align-items: center; gap: 8px; }
  .contact-line.indented { padding-left: 14px; }
  .contact-icon { width: 13px; height: 13px; flex: none; fill: var(--brand-deep); }
  .letter-body {
    position: absolute;
    left: 145px;
    top: 330px;
    width: 780px;
    font-size: 15.5px;
    line-height: 22px;
    letter-spacing: 0.3px;
  }
  .salutation { margin-bottom: 22px; }
  .letter-body p.paragraph { margin-bottom: 22px; }
  .closing { margin-top: 8px; }
  .signature-area {
    margin-top: 18px;
    width: 150px;
    height: 90px;
    background: var(--tint);
  }
  .footer-tagline {
    position: absolute;
    left: 0;
    right: 0;
    top: 1080px;
    display: flex;
    align-items: center;
    gap: 14px;
    padding: 0 0 0 50px;
  }
  .footer-rule { height: 2px; background: var(--rule); }
  .footer-rule.left { width: 360px; }
  .footer-rule.right { flex: 1; }
  .tagline-text {
    font-family: "Montserrat", Arial, sans-serif;
    font-weight: 600;
    font-size: 22px;
    letter-spacing: 0.5px;
    color: var(--brand-deep);
    text-transform: uppercase;
    white-space: nowrap;
  }
</style>
</head>
<body>
<div class="letterhead">

  <div class="brand">
    <div class="brand-square"></div>
    <div class="brand-name">Mesa Swift Serve</div>
  </div>

  <div class="contact">
    <div class="contact-line">4120 E Canyon Rd STE 210</div>
    <div class="contact-line">Sunvale AZ 85100</div>
    <div class="contact-line indented">
      <svg class="contact-icon" viewBox="0 0 16 16"><path d="M3.5 1l2.5 3-1.4 1.6a9 9 0 0 0 5.8 5.8L12 10l3 2.5-1.5 2.5C7 15 1 9 1 2.5z"/></svg>
      555-201-4830
    </div>
    <div class="contact-line indented">
      <svg class="contact-icon" viewBox="0 0 16 16"><path d="M4 1h8v4H4zM1 6h14v6h-3v3H4v-3H1zm4 4v4h6v-4z"/></svg>
      555-201-4831
    </div>
    <div class="contact-line indented">
      <svg class="contact-icon" viewBox="0 0 16 16"><path d="M1 3h14v1.5L8 9 1 4.5zM1 6.2l7 4.5 7-4.5V13H1z"/></svg>
      dana@mesaprocess.com
    </div>
    <div class="contact-line indented">
      <svg class="contact-icon" viewBox="0 0 16 16"><circle cx="8" cy="8" r="6.5" fill="none" stroke="#0e87c8" stroke-width="1.5"/><path d="M1.5 8h13M8 1.5c-3 3.5-3 9.5 0 13M8 1.5c3 3.5 3 9.5 0 13" fill="none" stroke="#0e87c8" stroke-width="1.2"/></svg>
      www.mesaprocess.com
    </div>
  </div>

  <div class="letter-body">
    <p class="salutation">Dear customer,</p>
    <p class="paragraph">Lorem ipsum dolor sit amet, consectetur adipisicing elit, sed do eiusmod tempor incididunt ut labore et dolore magna aliqua. Ut enim ad minim veniam, quis nostrud exercitation ullamco laboris nisi ut aliquip ex ea commodo consequat. Duis aute irure dolor in reprehenderit in voluptate velit esse cillum dolore eu fugiat nulla pariatur. Excepteur sint occaecat cupidatat non proident, sunt in culpa qui officia deserunt mollit anim id est laborum.</p>
    <p class="paragraph">Lorem ipsum dolor sit amet, consectetur adipisicing elit, sed do eiusmod tempor incididunt ut labore et dolore magna aliqua. Ut enim ad minim veniam, quis nostrud exercitation ullamco laboris nisi ut aliquip ex ea commodo consequat. Duis aute irure dolor in reprehenderit in voluptate velit esse cillum dolore eu fugiat nulla pariatur. Excepteur sint occaecat cupidatat non proident, sunt in culpa qui officia deserunt mollit anim id est laborum.</p>
    <p class="paragraph">Lorem ipsum dolor sit amet, consectetur adipisicing elit, sed do eiusmod tempor incididunt ut labore et dolore magna aliqua. Ut enim ad minim veniam, quis nostrud exercitation ullamco laboris nisi ut aliquip ex ea commodo consequat. Duis aute irure dolor in reprehenderit in voluptate velit esse cillum dolore eu fugiat nulla pariatur. Excepteur sint occaecat cupidatat non proident, sunt in culpa qui officia deserunt mollit anim id est laborum.</p>
    <p class="paragraph">Lorem ipsum dolor sit amet, consectetur adipisicing elit, sed do eiusmod tempor incididunt ut labore et dolore magna aliqua. Ut enim ad minim veniam, quis nostrud exercitation ullamco laboris nisi ut aliquip ex ea commodo consequat. Duis aute irure dolor in reprehenderit.</p>
    <p class="closing">Yours Sincerely,</p>
    <div class="signature-area" role="img" aria-label="Handwritten signature"></div>
  </div>

  <div class="footer-tagline">
    <div class="footer-rule left"></div>
    <div class="tagline-text">Process Service and Attorney Support</div>
    <div class="footer-rule right"></div>
  </div>

</div>
</body>
</html>
```